Stationery for Villa Marenta Design Hotel**

Who we are:

Wander on an isolated beach while breathing in the fresh, salty, sea air. Listen to the warm Pacific wind rustling through green palm trees as you walk to a pristine lagoon. Feel the delicious warmth of the sun kiss your skin; the beach is yours. At Villa Marenta you can experience a vacation in undisturbed, natural beauty. We have created a place for you to find new strength, relaxation, and inner harmony. We offer total rest to the experienced traveler from all over the world.

We are a brand new and smartly built design-hotel (under construction) close to a unique beach and a fantastic surf spot in Huatulco, Southwest Mexico.

As you can see in the attachments, we do have an established corporate design, but as for now still need a format for booklets for information around our hotel and things to do in the area, important numbers (we fill in the content for that one).

Our corporate colors:
green #64b445, brown #b07043, blue #0ab7cf, yellow # f9b02a and #fcc01a, navy #444f69
Corporate fonts:
Krub and Miller Banner.
For further information access:
www.villamarenta.example
https://slidevault.example/view/QmPxLwZrTyKsNbVcHdJe/

Social Media: VillaMarenta

Industry/Entity Type

Hotel

Font styles to use
Other font styles liked:
• Krub, Miller Banner

Requirements
Must have
• Stick to Logo Design, defined corporate elements, logo, colors, fonts and general touch and feel
Nice to have
• Who we are:

Our corporate colors:
Corporate fonts:
Krub and Miller Banner.
www.villamarenta.example

Social Media: VillaMarenta

```html
<!DOCTYPE html>
<html lang="en">
<head>
<meta charset="utf-8">
<title>Villa Marenta Design Hotel – Stationery</title>
<link rel="stylesheet" href="https://fonts.googleapis.com/css2?family=Krub:wght@400;500;600&family=Gelasio:wght@400&display=swap">
<style>
  :root {
    --green: #64b445;
    --brown: #b07043;
    --blue: #0ab7cf;
    --teal: #1f9aa3;
    --teal-dark: #17828a;
    --yellow: #f9b02a;
    --navy: #444f69;
    --paper: #ffffff;
    --ink: #5a5f66;
    --leaf-soft: #dcebcf;
    --stage: #aeb1bf;
    --liner: #86cb63;
  }
  * { margin: 0; padding: 0; box-sizing: border-box; }
  html, body { width: 1200px; height: 950px; overflow: hidden; }
  body { background: var(--stage); position: relative; font-family: "Gelasio", serif; }

  /* Compliment slip */
  .slip {
    position: absolute; left: 180px; top: 50px; width: 840px; height: 400px;
    background: var(--paper); overflow: hidden;
    box-shadow: 0 6px 18px rgba(40,45,70,.25);
  }
  .slip__leaf {
    position: absolute; right: 40px; top: 20px; width: 290px; height: 260px;
    border-radius: 55% 45% 50% 50% / 50% 55% 45% 50%;
    background: radial-gradient(circle at 45% 45%, #d3e7c2 0%, var(--leaf-soft) 60%, rgba(220,235,207,0) 100%);
    opacity: .85;
  }
  .brand { position: absolute; left: 40px; top: 36px; }
  .brand__mark { width: 78px; height: 78px; border: 2px solid var(--yellow); }
  .brand__name {
    font-family: "Krub", sans-serif; font-weight: 600; font-size: 20px;
    color: var(--yellow); letter-spacing: .04em; text-transform: uppercase; margin-top: 8px;
  }
  .brand__tagline {
    font-family: "Krub", sans-serif; font-size: 7px; color: var(--yellow);
    letter-spacing: .12em; text-transform: uppercase; margin-top: 2px;
  }
  .brand__address { font-size: 12px; color: var(--green); line-height: 1.25; margin-top: 4px; }

  .contact {
    position: absolute; left: 16px; bottom: 44px; display: flex; gap: 12px;
    font-size: 12px; color: var(--ink); align-items: center; white-space: nowrap;
  }
  .contact__item { display: flex; align-items: center; gap: 4px; }
  .contact__icon { width: 12px; height: 12px; flex: none; }

  .rule { position: absolute; bottom: 30px; height: 5px; }
  .rule--yellow { left: 0; width: 205px; background: var(--yellow); }
  .rule--green { left: 212px; width: 190px; background: var(--green); }
  .rule--brown { left: 409px; width: 225px; background: var(--brown); }
  .band { position: absolute; left: 0; right: 0; bottom: 12px; height: 13px; background: var(--teal); }
  .web-tab {
    position: absolute; right: 0; bottom: 12px; width: 190px; height: 62px;
    background: linear-gradient(var(--teal), var(--teal-dark));
    color: #fff; font-size: 14px; display: flex; align-items: center; justify-content: center;
    white-space: nowrap;
  }

  /* Envelope */
  .envelope {
    position: absolute; left: 180px; top: 500px; width: 840px; height: 400px;
    filter: drop-shadow(0 6px 14px rgba(40,45,70,.25));
  }
  .envelope svg { display: block; }
</style>
</head>
<body>

<section class="slip" aria-label="Compliment slip">
  <div class="slip__leaf" role="img" aria-label="Faint watercolour palm leaf decoration"></div>

  <div class="brand">
    <div class="brand__mark"></div>
    <div class="brand__name">Villa Marenta</div>
    <div class="brand__tagline">design hotel · surf · lagoon</div>
    <div class="brand__address">Playa Serena, Costa Azul,<br>Oaxaca, Mexiko</div>
  </div>

  <div class="contact">
    <span class="contact__item">
      <svg class="contact__icon" viewBox="0 0 12 12"><circle cx="6" cy="6" r="5.5" fill="none" stroke="var(--teal)"/><path d="M6 2.8a2 2 0 0 1 2 2c0 1.5-2 3.8-2 3.8S4 6.3 4 4.8a2 2 0 0 1 2-2z" fill="var(--teal)"/></svg>
      Playa Serena, Costa Azul, Oaxaca, Mexiko
    </span>
    <span class="contact__item">
      <svg class="contact__icon" viewBox="0 0 12 12"><circle cx="6" cy="6" r="5.5" fill="none" stroke="var(--teal)"/><path d="M4 3.2l1 1.4-.6.8a4 4 0 0 0 2.2 2.2l.8-.6 1.4 1-.6 1C6 9 3 6 3.2 4z" fill="var(--teal)"/></svg>
      +52 1 (555) 010 4477
    </span>
    <span class="contact__item">
      <svg class="contact__icon" viewBox="0 0 12 12"><circle cx="6" cy="6" r="5.5" fill="none" stroke="var(--teal)"/><rect x="3" y="4" width="6" height="4.2" fill="none" stroke="var(--teal)" stroke-width=".9"/><path d="M3 4l3 2.3L9 4" fill="none" stroke="var(--teal)" stroke-width=".9"/></svg>
      hello@villamarenta.example
    </span>
  </div>

  <div class="rule rule--yellow"></div>
  <div class="rule rule--green"></div>
  <div class="rule rule--brown"></div>
  <div class="band"></div>
  <div class="web-tab">www.villamarenta.example</div>
</section>

<section class="envelope" aria-label="Envelope, back with open flap">
  <svg width="840" height="400" viewBox="0 0 840 400">
    <path d="M0 120 L0 30 Q0 0 30 0 L810 0 Q840 0 840 30 L840 120 Z" fill="var(--liner)" role="img" aria-label="Green patterned flap liner"/>
    <path d="M0 120 Q60 100 150 100 L690 100 Q780 100 840 70 L840 400 L0 400 Z" fill="#f4f4f4"/>
    <path d="M25 400 L25 150 Q25 125 60 125 L780 125 Q815 125 815 150 L815 400" fill="none" stroke="#e2e2e2" stroke-width="1.5"/>
    <path d="M0 120 L0 400 L840 400 L840 70" fill="none" stroke="#e6e6e6"/>
  </svg>
</section>

</body>
</html>
```